Marlow Dermal Studio - Business Banner with Brand Elements

Design:
• We would like to get a creative design for a wide banner that will go outside our medical spa clinic location. We need a designer to make a simple yet colorful and high-quality design layout. We want this banner to be eye-catching and to communicate the services we offer at our business: Laser Hair Removal | Veluxin | Lip Filler.

Requirements:
• We would like the banner to include our companies information which is the following:

Logo
“Refresh Your Skin”
Laser Hair Removal | Veluxin | Lip Filler
(520) 867-2291
www.MarlowDermalStudio.com

Colors:
• Our business colors are orange, a hint of black and white, but mostly peach/orange tones. (Orange: #f78f20 , White: #ffffff)

Fonts:
• Josefins Sans Bold & Lato

Content and images can be located here:
https://files.quibbleshare.com/share/folders/7tKwP3zRa9_LmQxVb2nD5yHc04EeJuFs8?mode=viewing

The following will give you an idea of our brand presentation:
• Our website is: www.MarlowDermalStudio.com
• Our Pictavo; @marlowdermalstudio
• Our Lumora: www.lumoranet.com/marlowdermalstudio

Target Market(s)
• Women 25 - 45

Industry/Entity Type
• Beauty

```html
<!DOCTYPE html>
<html lang="en">
<head>
<meta charset="UTF-8">
<title>Marlow Dermal Studio – Outdoor Banner</title>
<link href="https://fonts.googleapis.com/css2?family=Josefin+Sans:wght@400;600;700&display=swap" rel="stylesheet">
<style>
  :root {
    --page-bg: #6d6d6d;
    --mint: #eefefc;
    --pink-light: #efdbe9;
    --pink: #efc4cb;
    --blush: #f4d3d8;
    --skin: #f1c1ad;
    --chair: #f4f1f0;
    --floor: #c9c3c6;
    --gold: #e9b44c;
    --gold-dark: #a5760f;
    --ink: #181b1f;
    --white: #ffffff;
  }
  * { margin: 0; padding: 0; box-sizing: border-box; }
  html, body {
    width: 1200px; height: 1000px; overflow: hidden;
    background: var(--page-bg);
    font-family: "Josefin Sans", sans-serif;
  }
  .banner {
    position: absolute; left: 95px; top: 303px;
    width: 1011px; height: 394px; overflow: hidden;
    background: var(--pink);
    box-shadow: 0 10px 22px rgba(0,0,0,0.25);
  }
  .banner__photo {
    position: absolute; inset: 0;
    background:
      linear-gradient(180deg, rgba(0,0,0,0) 375px, var(--floor) 385px, var(--floor) 394px),
      radial-gradient(ellipse 150px 120px at 260px 290px, rgba(244,241,240,0.85), rgba(244,241,240,0) 100%),
      radial-gradient(ellipse 130px 110px at 420px 290px, rgba(244,241,240,0.75), rgba(244,241,240,0) 100%),
      radial-gradient(ellipse 200px 150px at 230px 190px, rgba(241,193,173,0.75), rgba(241,193,173,0) 100%),
      radial-gradient(ellipse 210px 140px at 420px 180px, rgba(241,193,173,0.7), rgba(241,193,173,0) 100%),
      linear-gradient(100deg, var(--pink) 0%, var(--blush) 45%, var(--pink-light) 75%);
  }
  .banner__shapes { position: absolute; inset: 0; }
  .brand {
    position: absolute; left: 0; top: 18px; width: 144px;
    display: flex; flex-direction: column; align-items: center;
  }
  .brand__dot {
    width: 42px; height: 42px; border-radius: 50%;
    background: var(--gold); margin-bottom: 9px;
  }
  .brand__name {
    font-weight: 700; font-size: 19px; line-height: 1.05;
    color: var(--ink); text-align: center;
  }
  .headline {
    position: absolute; right: 52px; top: 46px;
    color: var(--ink); text-align: right; line-height: 1;
  }
  .headline__top { font-weight: 600; font-size: 63px; letter-spacing: 1px; display: block; }
  .headline__bottom { font-weight: 400; font-size: 51px; letter-spacing: 1px; display: block; margin-top: 2px; }
  .service {
    position: absolute; display: flex; align-items: center; gap: 14px;
    color: var(--white); font-size: 33px; font-weight: 400; line-height: 1;
  }
  .service__text { padding-top: 6px; }
  .icon-ring { width: 38px; height: 38px; flex: none; }
  .service--laser { left: 601px; top: 213px; }
  .service--veluxin { left: 601px; top: 264px; }
  .service--filler { left: 771px; top: 264px; }
  .contact {
    position: absolute; left: 483px; top: 338px;
    display: flex; align-items: center; gap: 8px;
    color: var(--white); font-size: 19px; font-weight: 600;
  }
  .contact__phone { font-size: 20px; }
  .contact__text { padding-top: 4px; }
  .contact__divider { width: 2px; height: 28px; background: var(--gold); margin: 0 6px; }
  .contact-icon { width: 26px; height: 26px; flex: none; }
</style>
</head>
<body>
  <section class="banner">
    <div class="banner__photo" role="img" aria-label="Photo of two women in white underwear sitting back to back on white chairs against a pink wall"></div>

    <svg class="banner__shapes" width="1011" height="394" viewBox="0 0 1011 394">
      <polygon points="0,0 235,0 0,280" fill="var(--mint)"/>
      <polygon points="685,0 1011,0 1011,175 542,175" fill="var(--gold)"/>
      <polygon points="542,175 597,175 567,202" fill="var(--gold-dark)"/>
      <polygon points="597,175 1011,175 1011,394 415,394" fill="var(--ink)"/>
    </svg>

    <div class="brand">
      <span class="brand__dot"></span>
      <span class="brand__name">Marlow<br>Dermal Studio</span>
    </div>

    <h1 class="headline">
      <span class="headline__top">REFRESH</span>
      <span class="headline__bottom">YOUR SKIN</span>
    </h1>

    <div class="service service--laser">
      <svg class="icon-ring" viewBox="0 0 38 38"><circle cx="19" cy="19" r="17" fill="none" stroke="var(--gold)" stroke-width="2.5"/><path d="M11 25h16M15 25l3-12M22 25l-2-10" stroke="var(--gold)" stroke-width="2" fill="none" stroke-linecap="round"/></svg>
      <span class="service__text">Laser Hair Removal</span>
    </div>
    <div class="service service--veluxin">
      <svg class="icon-ring" viewBox="0 0 38 38"><circle cx="19" cy="19" r="17" fill="none" stroke="var(--gold)" stroke-width="2.5"/><circle cx="19" cy="19" r="8" fill="var(--gold)"/><path d="M25 12l5-5" stroke="var(--gold)" stroke-width="2" stroke-linecap="round"/></svg>
      <span class="service__text">Veluxin</span>
    </div>
    <div class="service service--filler">
      <svg class="icon-ring" viewBox="0 0 38 38"><circle cx="19" cy="19" r="17" fill="none" stroke="var(--gold)" stroke-width="2.5"/><path d="M10 20c3-5 6-5 9-3 3-2 6-2 9 3-3 5-15 5-18 0z" fill="var(--gold)"/></svg>
      <span class="service__text">Lip Filler</span>
    </div>

    <div class="contact">
      <svg class="contact-icon" viewBox="0 0 26 26"><circle cx="13" cy="13" r="11.5" fill="none" stroke="var(--gold)" stroke-width="2"/><path d="M9 7.5l2.5 2.5-1.5 2c1 2 2 3 4 4l2-1.5 2.5 2.5-1.5 1.8C12 18.5 7.5 14 7.3 9z" fill="var(--gold)"/></svg>
      <span class="contact__text contact__phone">(520) 867-2291</span>
      <span class="contact__divider"></span>
      <svg class="contact-icon" viewBox="0 0 26 26"><circle cx="13" cy="13" r="11.5" fill="none" stroke="var(--gold)" stroke-width="2"/><circle cx="13" cy="13" r="7" fill="none" stroke="var(--gold)" stroke-width="1.5"/><ellipse cx="13" cy="13" rx="3" ry="7" fill="none" stroke="var(--gold)" stroke-width="1.5"/><path d="M6 13h14" stroke="var(--gold)" stroke-width="1.5"/></svg>
      <span class="contact__text">www.MarlowDermalStudio.com</span>
    </div>
  </section>
</body>
</html>
```